TalkHarbor - Language Coaching Services

Sleek, innovative, trendy design for Language Coaching business.

TalkHarbor is a new UK based company that provides Language Coaching services. We offer highly personalized on-line and face to face language courses. We also impart learning techniques workshops based on the latest neuroscience research for second-language acquisition.

Target Market(s)

See attached info

Industry/Entity Type

Consulting

Contact Information for Business Card

TalkHarbor
DaniaKV@talkharbor.co.uk
TalkHarbor.co.uk
London, UK

Font styles to use
Sans Serif

```html
<!DOCTYPE html>
<html lang="en">
<head>
<meta charset="utf-8">
<title>TalkHarbor – Business Card</title>
<link rel="stylesheet" href="https://fonts.googleapis.com/css2?family=Montserrat:wght@500&family=Open+Sans:wght@400;600&display=swap">
<style>
  :root {
    --stage: #e9e7e4;
    --card-dark: #2a2829;
    --card-light: #ffffff;
    --brand-blue: #1d8fc9;
    --ink: #2b2b2b;
    --text-light: #f2f2f2;
    --decor-grey: #ececec;
  }
  * { margin: 0; padding: 0; box-sizing: border-box; }
  html, body {
    width: 1200px; height: 900px; overflow: hidden;
    background: var(--stage);
    font-family: "Open Sans", Arial, sans-serif;
  }
  .stage { position: relative; width: 1200px; height: 900px; }

  .card {
    position: absolute;
    width: 700px; height: 400px;
    border-radius: 22px;
    overflow: hidden;
    box-shadow: 0 10px 30px rgba(0,0,0,0.18);
  }

  /* Back of card */
  .card--back {
    left: 250px; top: 30px;
    background: var(--card-dark);
    display: flex; flex-direction: column; align-items: center; justify-content: center;
  }
  .brand-mark {
    width: 118px; height: 118px;
    border: 7px solid var(--brand-blue);
    border-radius: 50%;
  }
  .card--back .wordmark {
    margin-top: 26px;
    font-family: "Montserrat", Arial, sans-serif;
    font-weight: 500;
    font-size: 62px;
    letter-spacing: 2px;
    color: var(--brand-blue);
    line-height: 1;
  }
  .card--back .site {
    margin-top: 34px;
    font-size: 20px;
    color: var(--text-light);
    letter-spacing: 0.5px;
  }

  /* Front of card */
  .card--front {
    left: 250px; top: 460px;
    background: var(--card-light);
  }
  .front-header {
    position: absolute; left: 40px; top: 34px;
    display: flex; align-items: center; gap: 22px;
  }
  .front-header .brand-mark { width: 96px; height: 96px; border-width: 6px; }
  .front-header .wordmark {
    font-family: "Montserrat", Arial, sans-serif;
    font-weight: 500;
    font-size: 42px;
    letter-spacing: 2px;
    color: var(--brand-blue);
  }
  .decor-disc {
    position: absolute; right: -70px; top: 110px;
    width: 360px; height: 360px;
    border-radius: 50%;
    background: var(--decor-grey);
  }
  .contact {
    position: absolute; left: 56px; top: 190px;
  }
  .contact__name {
    font-weight: 600; font-size: 22px;
    color: var(--brand-blue);
    margin-bottom: 14px;
  }
  .contact__list { list-style: none; }
  .contact__item {
    display: flex; align-items: center; gap: 16px;
    font-size: 19px; color: var(--ink);
    height: 31px;
  }
  .contact__item svg { width: 20px; height: 20px; fill: var(--brand-blue); flex: none; }
</style>
</head>
<body>
<main class="stage">

  <section class="card card--back" aria-label="Card back">
    <div class="brand-mark"></div>
    <div class="wordmark">TALKHARBOR</div>
    <div class="site">www.talkharbor.co.uk</div>
  </section>

  <section class="card card--front" aria-label="Card front">
    <div class="decor-disc"></div>
    <header class="front-header">
      <div class="brand-mark"></div>
      <div class="wordmark">TALKHARBOR</div>
    </header>
    <div class="contact">
      <p class="contact__name">TalkHarbor</p>
      <ul class="contact__list">
        <li class="contact__item">
          <svg viewBox="0 0 24 24" aria-hidden="true"><path d="M6.6 10.8a15.1 15.1 0 0 0 6.6 6.6l2.2-2.2a1 1 0 0 1 1-.25 11.4 11.4 0 0 0 3.6.57 1 1 0 0 1 1 1V20a1 1 0 0 1-1 1A17 17 0 0 1 3 4a1 1 0 0 1 1-1h3.5a1 1 0 0 1 1 1c0 1.25.2 2.45.57 3.57a1 1 0 0 1-.25 1z"/></svg>
          +44 1632 960718
        </li>
        <li class="contact__item">
          <svg viewBox="0 0 24 24" aria-hidden="true"><path d="M2 5h20v14H2z M2 5l10 8 10-8" fill="none" stroke="#1d8fc9" stroke-width="2"/></svg>
          DaniaKV@talkharbor.co.uk
        </li>
        <li class="contact__item">
          <svg viewBox="0 0 24 24" aria-hidden="true"><g fill="none" stroke="#1d8fc9" stroke-width="1.8"><circle cx="12" cy="12" r="9.5"/><ellipse cx="12" cy="12" rx="4" ry="9.5"/><path d="M2.5 12h19M4 7h16M4 17h16"/></g></svg>
          www.talkharbor.co.uk
        </li>
        <li class="contact__item">
          <svg viewBox="0 0 24 24" aria-hidden="true"><path d="M12 2a7 7 0 0 0-7 7c0 5.2 7 13 7 13s7-7.8 7-13a7 7 0 0 0-7-7zm0 9.5A2.5 2.5 0 1 1 12 6.5a2.5 2.5 0 0 1 0 5z"/></svg>
          London, UK
        </li>
      </ul>
    </div>
  </section>

</main>
</body>
</html>
```